Weightloss company needs Business Card

We want a business card that is clean and professional, yet portrays that we are a friendly, innovative, and versatile program designed to fit the needs of our clients.
I would like there to be 2 sides, one side having an appointment card, and the other side containing the logo and business information. There can be decorations on both sides. The logo is attached.

Target Market(s)

Men and women 40-60

Industry/Entity Type

Business

Contact Information for Business Card

Font styles to use
Sans Serif

Requirements
Must have
• The logo, space for business information
Nice to have
• The colors in the logo
Should not have
• No pictures of people or food

```html
<!DOCTYPE html>
<html lang="en">
<head>
<meta charset="utf-8">
<title>Turnaround Wellness – Business Card</title>
<link href="https://fonts.googleapis.com/css2?family=Open+Sans:wght@400;600;700&display=swap" rel="stylesheet">
<style>
  :root {
    --backdrop: #2b2b2d;
    --card-white: #ffffff;
    --card-black: #050505;
    --brand-red: #e8263f;
    --brand-blue: #35b8e6;
    --ink: #1d1d1d;
    --rule: #3a3a3a;
    --text-light: #ffffff;
  }
  * { box-sizing: border-box; margin: 0; padding: 0; }
  html, body {
    width: 1200px;
    height: 900px;
    overflow: hidden;
    background: var(--backdrop);
    font-family: "Open Sans", Arial, sans-serif;
  }
  .card {
    position: absolute;
    width: 620px;
    height: 354px;
    border-radius: 22px;
    box-shadow: 0 18px 40px rgba(0,0,0,0.45);
    overflow: hidden;
  }

  /* Appointment side */
  .card--appointment {
    left: 90px;
    top: 80px;
    background: var(--card-white);
    color: var(--ink);
  }
  .appointment__title {
    position: absolute;
    left: 44px;
    top: 104px;
    font-size: 14px;
    font-weight: 600;
    color: var(--brand-red);
    letter-spacing: 0.3px;
  }
  .appointment__row {
    position: absolute;
    display: flex;
    align-items: flex-end;
    gap: 8px;
    font-size: 15px;
  }
  .appointment__row--name { top: 134px; left: 58px; }
  .appointment__row--date { top: 182px; left: 86px; }
  .appointment__row--time { top: 230px; left: 114px; }
  .appointment__line {
    display: block;
    width: 300px;
    border-bottom: 1px solid var(--rule);
    margin-bottom: 4px;
  }
  .card--appointment .brand {
    position: absolute;
    right: 40px;
    bottom: 22px;
  }

  /* Brand name block */
  .brand {
    display: flex;
    align-items: center;
    gap: 12px;
  }
  .brand__mark {
    width: 22px;
    height: 22px;
    border-radius: 50%;
    background: var(--brand-red);
    flex-shrink: 0;
  }
  .brand__name {
    font-size: 30px;
    font-weight: 700;
    line-height: 1.05;
    color: var(--brand-red);
  }

  /* Contact side */
  .card--contact {
    left: 490px;
    top: 470px;
    background: var(--card-black);
    color: var(--text-light);
  }
  .contact__ring {
    position: absolute;
    right: 58px;
    top: 34px;
    width: 128px;
    height: 128px;
    border-radius: 50%;
    border: 6px solid var(--text-light);
  }
  .contact__tab {
    position: absolute;
    left: 0;
    top: 160px;
    width: 10px;
    height: 34px;
    background: var(--text-light);
  }
  .card--contact .brand {
    position: absolute;
    left: 44px;
    top: 60px;
  }
  .contact__person {
    position: absolute;
    left: 44px;
    top: 160px;
  }
  .contact__name {
    font-size: 22px;
    font-weight: 400;
    color: var(--brand-red);
    text-transform: uppercase;
    letter-spacing: 0.5px;
  }
  .contact__role {
    font-size: 13px;
    font-weight: 600;
    color: var(--brand-blue);
    text-transform: uppercase;
    margin-top: 2px;
  }
  .contact__address {
    margin-top: 8px;
    font-size: 15px;
    line-height: 1.35;
  }
  .contact__list {
    position: absolute;
    left: 44px;
    top: 268px;
    list-style: none;
    font-size: 15px;
  }
  .contact__item {
    display: flex;
    align-items: center;
    gap: 10px;
    line-height: 1.45;
  }
  .contact__icon {
    width: 14px;
    height: 14px;
    flex-shrink: 0;
  }
</style>
</head>
<body>

  <section class="card card--appointment" aria-label="Appointment side">
    <p class="appointment__title">APPOINTMENT</p>
    <div class="appointment__row appointment__row--name"><span>Name:</span><span class="appointment__line"></span></div>
    <div class="appointment__row appointment__row--date"><span>Date:</span><span class="appointment__line"></span></div>
    <div class="appointment__row appointment__row--time"><span>Time:</span><span class="appointment__line"></span></div>
    <div class="brand">
      <span class="brand__mark"></span>
      <span class="brand__name">Turnaround<br>Wellness</span>
    </div>
  </section>

  <section class="card card--contact" aria-label="Contact side">
    <span class="contact__ring"></span>
    <span class="contact__tab"></span>
    <div class="brand">
      <span class="brand__mark"></span>
      <span class="brand__name">Turnaround<br>Wellness</span>
    </div>
    <div class="contact__person">
      <p class="contact__name">Marcus Hale</p>
      <p class="contact__role">Director</p>
      <p class="contact__address">Cedar Lane, 40210<br>Harbor City, Westland</p>
    </div>
    <ul class="contact__list">
      <li class="contact__item">
        <svg class="contact__icon" viewBox="0 0 16 16" aria-hidden="true"><path d="M3 1.5l3 3-1.6 1.8a9 9 0 0 0 5.3 5.3L11.5 10l3 3-1.8 2C6.5 15 1 9.5 1 3.3z" fill="var(--brand-red)"/></svg>
        <span>+330 5550-1482</span>
      </li>
      <li class="contact__item">
        <svg class="contact__icon" viewBox="0 0 16 16" aria-hidden="true"><rect x="1" y="3" width="14" height="10" fill="none" stroke="var(--brand-red)" stroke-width="1.6"/><path d="M1.5 3.5L8 9l6.5-5.5" fill="none" stroke="var(--brand-red)" stroke-width="1.6"/></svg>
        <span>info@turnaroundwellness.com</span>
      </li>
      <li class="contact__item">
        <svg class="contact__icon" viewBox="0 0 16 16" aria-hidden="true"><circle cx="8" cy="8" r="6.8" fill="none" stroke="var(--brand-red)" stroke-width="1.4"/><ellipse cx="8" cy="8" rx="3" ry="6.8" fill="none" stroke="var(--brand-red)" stroke-width="1.2"/><path d="M1.2 8h13.6M2.5 4.5h11M2.5 11.5h11" stroke="var(--brand-red)" stroke-width="1.1"/></svg>
        <span>www.turnaroundwellness.com</span>
      </li>
    </ul>
  </section>

</body>
</html>
```